Snapnook needs You

Help us create an inviting, amazing, sleek, simple, clear landing page for a picture-memory-social connection site!

Business Name: SnapNook
Industry: Social Networking and Creativity through Pictures
A web platform for and about a community that is driven by a passion for sharing, caring, bonding, collaborating, creating and earning with pictures, through pictures and other related creative activities. This is going to be a great site for all creative artists-photographers, artists, graphic artists to express their work and their creativity.

The main focus of the site is - CONNECTIONS.
This will be uncoded.

Desired Website Screen Size
1024x768... Widescreen/Landscape orientation, is what we mean... So it fits on a CPU screen.

Desired look and feel and message
Look: Visitor should feel immersed in the page, in the world the page creates, simple, elegant, sophisticated, contemporary. We really like a clean uncluttered look.

Special mention: By the way we love the marketing genius who thought up this branding for velu yogurt where they used the two dots above the o to create a branding effect that made this brand instantly identifiable. http://www.velu-dairy.ca/en/

The two dots by themselves without having even the name present brings up the whole brand now. The dots are used above all the ingredients of the yogurt creating friendly figures, and above people in commercials-bringing the people onto the side of "team" velu. Snapnook may have a character created or something distinctive in the letters in the name created to brand the site as well.

Feel: Engaging; Magical without being corny, here is a link to give an example look and feel but please do not be hindered in your creativity by this suggestion. We love all creative angles.
http://artscrapyard.com/graphic/5829317-camera-film-roll-blue-background

Message: Life and memories and connections through pictures.

Target audience:
The site is focused on pictures but not confined to photography enthusiasts (although they are an integral part of the site). Customers/Visitors will include families, corporates and the younger generation - all age groups, all class, everyone with pictures to express, memories to share.

Website design we like:
http://brindlework.com/work/northern-ballet-house/
http://brindlework.com/work/zapverse/

What colors do we want to see on our landing page?
We would like the background to be grey or blue since it is grey is picture neutral colour and blue highlights pictures well and we also like blue and silver, which can be integrated into the theme. Also like green. But please do not let these instructions limit your creativity. We are open to new ideas and colours.

Predetermined Concepts if any:
We have a concept in mind and we think it would be cool to have an interface for the user through the back of a camera on the landing page -This could be used to create a scene or world the visitor feels a part of or is immersed into. The back screen of the camera may act as a screen for the slideshow of featured pictures on the site.

Content on the Page:
Photo Gallery with full screen, thumbnail view, zoom option etc.
Prominent but short introductory message
Sign in / Login Options
Links: Home Page; About; Info/Help; Contact Us; Privacy Policy; Terms of Use
At the bottom of the page: Follow Me/Like/Workplaza...social buttons.

Please feel free to add any other element to the landing page that you think might add to the effect of simple yet amazing look -clean, simple, uncluttered, sophisticated, stylish, inviting and engaging.
The concept is a guideline, but we would like you to be as creative as you can, even if it meant stepping out of these guidelines - rethink design, style, content if you like. We believe in bringing a solution in an innovative yet simple and elegant style. Something a visitor would be intrigued enough to explore and the guest would feel comfortable enough taking that step forward to have fun on the site. If you believe in the same, and you have the skill then you will have what we need. Good luck, go for it and we are excited to see what the amazing designers on this amazing site have to offer.
If you have any questions please free to ask.

HI wanted to send an update that this project design has been guaranteed.

Our site will be one to celebrate and showcase imagination as well as connection.  We would love to see what you create. Keep in mind our site will showcase all creativity, photographs, artists, graphic artists so this would be a benefit you may want to take advantage of in the future, a place where, if you so choose, you could gain exposure for your work. Therefore, even if you do not win the design project there is possible future benefit.

Imagination is everything.
Imagination encircles the world.-Halvorsen

Reason: We are giving the designers who accepted invites but have not yet submitted a chance to finish their submissions and the ones who are working on revisions a chance to finish those:)

Hello everyone,

Due to time constraints we must come to a decision sooner than the deadline of 28th. 

So, please try to submit any new designs or modifications to the old ones before the 26th. We are very thankful to all of you who have participated - for your designs, enthusiasm and kind words. 

Good luck! :)

• Thank you for the interest shown and your submissions! Designers who have submitted up until now have shown great potential. We are VERY excited with the quality of work and designs.

We want to add that Snapnook is not exclusively for the photographers. The site is for every person who may have a picture to store, organise, use or share - whether publicly or with only a few friends and family.

Snapnook is about allowing people to take control of their creativity. It is about providing tools to our users so that they can build their own connections and social network... of friends, family, fans, clients, ideas, thoughts, emotions etc. through pictures without worrying about their privacy or control over their creations.

With this update we want to encourage others to go beyond the camera theme. Do not let us restrict your creativity. Let YOUR OWN ideas take over if that’s what you think will best convey the message and will appeal to the users.

```html
<!DOCTYPE html>
<html lang="en">
<head>
<meta charset="utf-8">
<title>SnapNook — Professional Photo</title>
<link href="https://fonts.googleapis.com/css2?family=Arimo:ital,wght@0,400;0,700;1,400;1,700&display=swap" rel="stylesheet">
<style>
  :root {
    --accent-orange: #f5a21b;
    --hero-dark: #3a3a3a;
    --hero-mid: #545454;
    --text-light: #ffffff;
    --text-dark: #222222;
    --text-muted: #444444;
    --nav-blue: #0aa0e0;
    --nav-blue-deep: #0785bd;
    --footer-dark: #3b3b3b;
    --footer-text: #d0d0d0;
    --field-dark: #2b2b2b;
    --social-tile: #8a8a8a;
  }
  * { box-sizing: border-box; margin: 0; padding: 0; }
  html, body { width: 1200px; height: 740px; overflow: hidden; background: #fff; }
  body { font-family: "Arimo", Arial, sans-serif; position: relative; }

  .top-strip { position: absolute; left: 0; top: 0; width: 1200px; height: 4px; background: var(--accent-orange); }

  .hero {
    position: absolute; left: 0; top: 4px; width: 1200px; height: 480px;
    background: radial-gradient(ellipse 520px 420px at 560px 250px, #6a6a6a 0%, var(--hero-mid) 45%, var(--hero-dark) 100%);
  }

  .brand { position: absolute; left: 213px; top: 56px; display: flex; align-items: baseline; gap: 12px; color: var(--text-light); }
  .brand-name { font-size: 27px; font-weight: 400; letter-spacing: 0.5px; }
  .brand-tagline { font-size: 11px; font-style: italic; letter-spacing: 0.3px; }

  .social { position: absolute; left: 710px; top: 63px; display: flex; gap: 2px; }
  .social span { width: 16px; height: 16px; background: var(--social-tile); border-radius: 2px; }

  .search-icon { position: absolute; left: 790px; top: 62px; }
  .search-field {
    position: absolute; left: 817px; top: 58px; width: 183px; height: 23px;
    background: var(--field-dark); border-radius: 4px; box-shadow: inset 0 1px 3px rgba(0,0,0,.6);
    color: var(--text-light); font-size: 14px; font-style: italic; padding: 3px 8px;
  }

  .slide { position: absolute; }
  .slide-main { left: 340px; top: 144px; width: 493px; height: 264px;
    background: radial-gradient(ellipse at 50% 55%, #7a3a1f 0%, #8c7a2e 35%, #5c4a25 70%, #3a2e18 100%); }
  .slide-prev { left: 0; top: 200px; width: 248px; height: 167px;
    background: linear-gradient(160deg, #a9b3bd 0%, #7e8b97 45%, #5f6b77 100%); }
  .slide-next { left: 956px; top: 200px; width: 244px; height: 164px;
    background: linear-gradient(180deg, #8b96a1 0%, #4f5e6e 50%, #8a949d 100%); }

  .arrow { position: absolute; top: 270px; }
  .arrow-prev { left: 270px; }
  .arrow-next { left: 898px; }

  .promo-band {
    position: absolute; left: 0; top: 484px; width: 1200px; height: 103px;
    background: linear-gradient(180deg, #f6f6f6 0%, #ffffff 30%, #ececec 100%);
  }
  .promo { position: absolute; }
  .promo-1 { left: 275px; top: 38px; }
  .promo-2 { left: 634px; top: 36px; }
  .promo-go {
    position: absolute; left: 0; top: 10px; width: 20px; height: 20px; border-radius: 50%;
    background: radial-gradient(circle at 40% 35%, #3fb4ec 0%, #0a6ea8 80%);
    color: #fff; font-size: 8.5px; font-style: italic; text-align: center; line-height: 20px;
  }
  .promo-title { position: absolute; left: 38px; top: -6px; font-size: 22px; color: var(--text-dark); white-space: nowrap; }
  .promo-text { position: absolute; left: 34px; top: 21px; font-size: 12.5px; font-style: italic; color: var(--text-muted); white-space: nowrap; }
  .promo-2 .promo-title { left: 42px; top: -6px; }
  .promo-2 .promo-text { left: 42px; top: 19px; }

  .nav-bar {
    position: absolute; left: 0; top: 587px; width: 1200px; height: 36px;
    background: linear-gradient(180deg, #13aae6 0%, var(--nav-blue) 60%, var(--nav-blue-deep) 100%);
  }
  .nav-tab {
    position: absolute; top: 0; height: 36px; transform: skewX(-14deg);
    background: linear-gradient(90deg, rgba(0,0,0,.12) 0%, rgba(255,255,255,0) 40%);
  }
  .nav-link { position: absolute; top: 8px; color: var(--text-light); font-size: 17px; text-decoration: none; }
  .nav-marker { position: absolute; left: 334px; top: 30px; width: 14px; height: 7px; background: #3b3b3b; border-radius: 7px 7px 0 0; }

  .signin-label { position: absolute; left: 745px; top: 8px; color: var(--text-light); font-size: 17px; font-style: italic; }
  .signin-field {
    position: absolute; left: 824px; top: 7px; width: 146px; height: 22px; border-radius: 4px;
    background: var(--nav-blue-deep); box-shadow: inset 0 1px 3px rgba(0,0,0,.45);
    color: var(--text-light); font-size: 14px; font-style: italic; padding: 3px 9px;
  }
  .signin-go { position: absolute; left: 981px; top: 8px; color: var(--text-light); font-size: 15px; font-style: italic; }

  .footer {
    position: absolute; left: 0; top: 623px; width: 1200px; height: 38px;
    background: linear-gradient(180deg, #2e2e2e 0%, var(--footer-dark) 100%);
    display: flex; justify-content: center; align-items: center; gap: 10px; padding-left: 10px;
  }
  .footer-text { color: var(--footer-text); font-size: 9.5px; font-style: italic; }
  .footer-brand { color: var(--text-light); font-size: 14px; }
</style>
</head>
<body>
  <div class="top-strip"></div>

  <header class="hero" role="img" aria-label="Soft grey backdrop with a faded camera and film roll">
  </header>

  <div class="brand">
    <span class="brand-name">SNAPNOOK</span>
    <span class="brand-tagline">PROFESHIONAL PHTO</span>
  </div>

  <div class="social" aria-label="Social links">
    <span></span><span></span><span></span><span></span>
  </div>

  <svg class="search-icon" width="20" height="20" viewBox="0 0 20 20" aria-hidden="true">
    <circle cx="12" cy="7.5" r="5" fill="none" stroke="#28a8e6" stroke-width="2.5"/>
    <line x1="8.5" y1="11" x2="3" y2="16.5" stroke="#28a8e6" stroke-width="3" stroke-linecap="round"/>
  </svg>
  <div class="search-field">Search</div>

  <div class="slide slide-prev" role="img" aria-label="Photo of snowy mountain slopes"></div>
  <div class="slide slide-main" role="img" aria-label="Featured photo of a chestnut in its spiky husk"></div>
  <div class="slide slide-next" role="img" aria-label="Photo of a dark sea channel between ice"></div>

  <svg class="arrow arrow-prev" width="22" height="22" viewBox="0 0 22 22" aria-label="Previous">
    <polyline points="16,2 6,11 16,20" fill="none" stroke="#f5a21b" stroke-width="5"/>
  </svg>
  <svg class="arrow arrow-next" width="22" height="22" viewBox="0 0 22 22" aria-label="Next">
    <polyline points="6,2 16,11 6,20" fill="none" stroke="#f5a21b" stroke-width="5"/>
  </svg>

  <section class="promo-band">
    <div class="promo promo-1">
      <span class="promo-go">GO</span>
      <span class="promo-title">SNAPNOOK</span>
      <span class="promo-text">Te dicam labitur mel, est eu graeco minimum,</span>
    </div>
    <div class="promo promo-2">
      <span class="promo-go">GO</span>
      <span class="promo-title">SNAPNOOK</span>
      <span class="promo-text">Te dicam labitur mel, est eu graeco minimum,</span>
    </div>
  </section>

  <nav class="nav-bar">
    <div class="nav-tab" style="left:212px;width:93px"></div>
    <div class="nav-tab" style="left:305px;width:93px"></div>
    <div class="nav-tab" style="left:398px;width:85px"></div>
    <div class="nav-tab" style="left:483px;width:82px"></div>
    <a class="nav-link" href="#" style="left:229px">home</a>
    <a class="nav-link" href="#" style="left:313px">products</a>
    <a class="nav-link" href="#" style="left:413px">about</a>
    <a class="nav-link" href="#" style="left:498px">contact</a>
    <span class="nav-marker"></span>
    <span class="signin-label">SIGN IN</span>
    <div class="signin-field">email</div>
    <span class="signin-go">GO</span>
  </nav>

  <footer class="footer">
    <span class="footer-text">minimum, in sit facer assueverit inciderint.</span>
    <span class="footer-brand">SNAPNOOK</span>
    <span class="footer-text">minimum, in sit facer assueverit inciderint.</span>
  </footer>
</body>
</html>
```